Landing Page / Waitlist

I would like a landing page for people to sign up for a waiting list. The text on the page should include (but is not limited to):
1) Main point: The accounting system you'll love
2) Secondary points:
a. Ruthlessly efficient
b. Quietly intelligent
c. Driven by AI
I've attached a file of our logo

The design should be simple, clean, and innovative - this is an ai company

```html
<!DOCTYPE html>
<html lang="en">
<head>
<meta charset="UTF-8">
<title>LedgerNova — Waiting List</title>
<link href="https://fonts.googleapis.com/css2?family=Red+Hat+Display:wght@400;500;700&display=swap" rel="stylesheet">
<style>
  :root {
    --stage: #03051a;
    --white: #ffffff;
    --ink: #0b0b12;
    --brand-grey: #6f7178;
    --accent: #00b4f5;
    --accent-deep: #0a8ff0;
    --navy: #050d66;
    --navy-deep: #020848;
    --field-line: #d9ecf7;
    --placeholder: #9aa3ad;
    --light-text: #eef4ff;
  }
  * { box-sizing: border-box; margin: 0; padding: 0; }
  html, body {
    width: 1015px; height: 1200px; overflow: hidden;
    background: var(--stage);
    font-family: "Red Hat Display", sans-serif;
  }
  .board { position: relative; width: 1015px; height: 1200px; }

  .page {
    position: absolute; left: 80px; width: 855px; height: 487px;
    overflow: hidden;
  }
  .page--light { top: 71px; background: linear-gradient(170deg, #e6f3fc 0%, var(--white) 22%); }
  .page--dark { top: 625px; background: radial-gradient(circle at 70% 40%, var(--navy) 0%, var(--navy-deep) 100%); }

  .hero { position: absolute; top: 0; }
  .page--light .hero { left: 78px; }
  .page--dark .hero { left: 439px; top: 7px; }

  .brand-name {
    position: absolute; top: 78px; left: 0;
    font-size: 25px; font-weight: 700; letter-spacing: -0.3px; white-space: nowrap;
  }
  .page--light .brand-name { color: var(--brand-grey); }
  .page--dark .brand-name { top: 94px; color: var(--white); }

  .headline { position: absolute; top: 155px; left: 0; white-space: nowrap; }
  .headline__main {
    display: block; font-size: 34px; font-weight: 700; letter-spacing: -0.4px; line-height: 40px;
  }
  .headline__accent {
    display: block; font-size: 42px; font-weight: 400; color: var(--accent); line-height: 44px; margin-top: -1px;
  }
  .page--light .headline__main { color: var(--ink); }
  .page--dark .headline__main { color: var(--white); }

  .features { position: absolute; top: 256px; left: 0; list-style: none; white-space: nowrap; }
  .features li {
    display: flex; align-items: center; gap: 8px;
    height: 30.5px; font-size: 14.5px; font-weight: 500;
  }
  .page--light .features li { color: var(--ink); }
  .page--dark .features li { color: var(--light-text); }
  .features svg { width: 11px; height: 12px; flex: none; }

  .signup {
    position: absolute; top: 356px; left: 1px; width: 326px; height: 38px;
    border-radius: 19px; background: var(--white);
    border: 1px solid var(--field-line);
    box-shadow: 0 4px 14px rgba(0, 150, 230, 0.08);
  }
  .signup__field {
    position: absolute; left: 18px; top: 11px;
    font-size: 10px; color: var(--placeholder);
  }
  .signup__button {
    position: absolute; right: 3px; top: 3px; width: 123px; height: 30px;
    border-radius: 15px; background: linear-gradient(90deg, var(--accent-deep), var(--accent));
    color: var(--white); font-family: inherit; font-size: 10px; font-weight: 500;
    border: none; display: flex; align-items: center; justify-content: center;
  }

  .artwork { position: absolute; }
  .page--light .artwork {
    left: 417px; top: 87px; width: 430px; height: 293px;
    background: radial-gradient(ellipse 34% 50% at 58% 52%, #1e9cf0 0%, #2a78e8 55%, rgba(230,238,252,0.6) 70%, rgba(255,255,255,0) 100%);
  }
  .page--dark .artwork {
    left: 0; top: 0; width: 438px; height: 457px;
    background: radial-gradient(ellipse 48% 46% at 58% 52%, #26b8ff 0%, #0a62f0 45%, #0634b8 72%, rgba(5,13,102,0) 100%);
  }

  .footer-band {
    position: absolute; left: 0; bottom: 0; width: 100%; height: 30px;
    background: var(--accent);
    display: flex; align-items: center; justify-content: center;
    color: var(--white); font-size: 11px; font-weight: 700;
  }
</style>
</head>
<body>
<div class="board">

  <section class="page page--light">
    <div class="artwork" role="img" aria-label="Blue sphere labelled AI inside a light network of connected nodes, with small floating cones"></div>
    <div class="hero">
      <div class="brand-name">LedgerNova</div>
      <h1 class="headline">
        <span class="headline__main">The Accounting System</span>
        <span class="headline__accent">You'll Love</span>
      </h1>
      <ul class="features">
        <li><svg viewBox="0 0 11 12"><path d="M1.5 1.5 L9.5 6 L1.5 10.5 Z" fill="none" stroke="#00b4f5" stroke-width="1.6" stroke-linejoin="round"/></svg>Ruthlessly efficient</li>
        <li><svg viewBox="0 0 11 12"><path d="M1.5 1.5 L9.5 6 L1.5 10.5 Z" fill="none" stroke="#00b4f5" stroke-width="1.6" stroke-linejoin="round"/></svg>Quietly intelligent</li>
        <li><svg viewBox="0 0 11 12"><path d="M1.5 1.5 L9.5 6 L1.5 10.5 Z" fill="none" stroke="#00b4f5" stroke-width="1.6" stroke-linejoin="round"/></svg>Driven by AI</li>
      </ul>
      <div class="signup">
        <span class="signup__field">Enter The Email</span>
        <button class="signup__button">Join Our Waiting list</button>
      </div>
    </div>
    <footer class="footer-band">Copyrights@2025.LedgerNova.All Rights Reserved</footer>
  </section>

  <section class="page page--dark">
    <div class="artwork" role="img" aria-label="Glowing blue flowing-line wave surrounding large white AI lettering with the words artificial intelligence"></div>
    <div class="hero">
      <div class="brand-name">LedgerNova</div>
      <h1 class="headline">
        <span class="headline__main">The Accounting System</span>
        <span class="headline__accent">You'll Love</span>
      </h1>
      <ul class="features">
        <li><svg viewBox="0 0 11 12"><path d="M1.5 1.5 L9.5 6 L1.5 10.5 Z" fill="none" stroke="#00b4f5" stroke-width="1.6" stroke-linejoin="round"/></svg>Ruthlessly efficient</li>
        <li><svg viewBox="0 0 11 12"><path d="M1.5 1.5 L9.5 6 L1.5 10.5 Z" fill="none" stroke="#00b4f5" stroke-width="1.6" stroke-linejoin="round"/></svg>Quietly intelligent</li>
        <li><svg viewBox="0 0 11 12"><path d="M1.5 1.5 L9.5 6 L1.5 10.5 Z" fill="none" stroke="#00b4f5" stroke-width="1.6" stroke-linejoin="round"/></svg>Driven by AI</li>
      </ul>
      <div class="signup">
        <span class="signup__field">Enter The Email</span>
        <button class="signup__button">Join Our Waiting list</button>
      </div>
    </div>
    <footer class="footer-band">Copyrights@2025.LedgerNova.All Rights Reserved</footer>
  </section>

</div>
</body>
</html>
```